Coffee Bag Label design for Australian Firefighter brand

I need a label for coffee bags. Front and back. We are based in Australia and aimed at Firefighters and First responders. I will have three size available. 250g, 500g and 1kg. So if we can use the same label that would be great. maybe a check box option at the bottom with the three sizes.
I really like the design for Lanyard Coffee (see attached), so I'm hoping for something along the same lines. replacing the images with firefighter axe, hose, halagan tool, cutting gear etc
I would like to include 'Firefighter founded" on the front, as well as 'Copper Ridge Blend'. Roasted med-dark on the Sunshine Coast, QLD
On the back I need space for a qr code with an arrow pointing to it with handwritten font 'how're you travelling? Free, confidential wellness check in'
and the text;
Coffee without the b.s.
This ain’t the sort of coffee for your average piccolo drinking, man-bun enthusiast. No fancy rose petal and unicorn pube infusions here. Just consistently great coffee that shows up, for those who show up. Firefighter founded and built with the Australian First Responder in mind.
Your life is complicated enough. Your coffee shouldn’t be.
For more, go to bluekettleroast.com.au or scan the QR code for a free, fast, confidential mental wellness check-in and useful resources.
These will be printed as sticker lables to go on kraft black coffee bags to begin with. Please see attached bag example and logo for use.
Target Market(s)
Australian Firefighters and First responders
Look and feel

```html
<!DOCTYPE html>
<html lang="en">
<head>
<meta charset="utf-8">
<title>Ember Watch Coffee – Copper Ridge Blend Label</title>
<link href="https://fonts.googleapis.com/css2?family=Oswald:wght@500;700&family=Kalam:wght@400&display=swap" rel="stylesheet">
<style>
  :root {
    --page: #ffffff;
    --bag: #232222;
    --bag-edge: #1a1a1a;
    --cream: #e8d8b6;
    --red: #9c1a1e;
    --maroon: #5e1520;
  }
  * { box-sizing: border-box; margin: 0; padding: 0; }
  html, body { width: 1200px; height: 957px; overflow: hidden; background: var(--page); }
  .canvas { position: relative; width: 1200px; height: 957px; }

  .label {
    position: absolute; left: 290px; top: 70px; width: 620px; height: 817px;
    background: radial-gradient(ellipse at 45% 40%, #2c2b2a 0%, var(--bag) 60%, var(--bag-edge) 100%);
    border-radius: 6px;
    color: var(--cream);
    font-family: "Oswald", sans-serif;
  }

  .brand {
    position: absolute; top: 150px; left: 0; right: 0;
    display: flex; align-items: center; justify-content: center; gap: 16px;
  }
  .brand-dot { width: 34px; height: 34px; border-radius: 50%; background: var(--cream); }
  .brand-name {
    font-weight: 700; font-size: 52px; letter-spacing: 1px; text-transform: uppercase; line-height: 1;
  }

  .hero-art {
    position: absolute; left: 58px; top: 250px; width: 330px; height: 270px;
    border-radius: 14px;
    background: radial-gradient(ellipse at 55% 55%, var(--cream) 0%, #b58a7a 40%, var(--maroon) 70%, rgba(156,26,30,0) 100%);
  }

  .blend-box {
    position: absolute; left: 378px; top: 262px; width: 214px; height: 230px;
    border: 3px solid var(--cream);
    padding: 14px 16px 0 30px;
  }
  .blend-star { position: absolute; left: 10px; top: 14px; font-size: 22px; line-height: 1; }
  .blend-name {
    font-weight: 700; font-size: 40px; line-height: 1.06; text-transform: uppercase;
  }
  .roast {
    position: absolute; left: 14px; right: 0; bottom: 12px;
    border-top: 3px solid var(--cream); padding-top: 8px;
    font-weight: 500; font-size: 17px; text-transform: uppercase; text-align: center;
  }

  .origin {
    position: absolute; left: 122px; top: 560px;
    font-family: "Kalam", cursive; font-size: 21px;
  }

  .founded {
    position: absolute; left: 122px; top: 612px; width: 362px; height: 60px;
    border: 3px solid var(--cream);
    display: flex; align-items: center; justify-content: center;
    font-weight: 700; font-size: 24px; text-transform: uppercase; letter-spacing: 0.5px;
  }

  .cert-badge {
    position: absolute; left: 496px; top: 588px; width: 100px; height: 100px;
    border-radius: 50%; border: 2px solid var(--cream);
  }

  .sizes {
    position: absolute; top: 716px; left: 0; right: 0;
    display: flex; justify-content: center; gap: 30px;
    font-weight: 700; font-size: 22px;
  }
  .size { display: flex; align-items: center; gap: 8px; }
  .size-box { width: 22px; height: 22px; border: 2px solid var(--cream); }
</style>
</head>
<body>
<main class="canvas">
  <section class="label">
    <header class="brand">
      <span class="brand-dot"></span>
      <span class="brand-name">Ember Watch Coffee</span>
    </header>

    <div class="hero-art" role="img" aria-label="Illustration of a red fire axe and halligan bar crossed over a rolled fire hose and rescue cutting saw"></div>

    <div class="blend-box">
      <span class="blend-star">★</span>
      <h1 class="blend-name">Copper<br>Ridge<br>Blend</h1>
      <p class="roast">Medium-Dark Roast</p>
    </div>

    <p class="origin">Roasted on the Sunshine Coast, QLD.</p>

    <p class="founded">Firefighter Founded</p>

    <div class="cert-badge" role="img" aria-label="Certification badge"></div>

    <ul class="sizes">
      <li class="size"><span class="size-box"></span>250g</li>
      <li class="size"><span class="size-box"></span>500g</li>
      <li class="size"><span class="size-box"></span>1kg</li>
    </ul>
  </section>
</main>
</body>
</html>
```